Real Estate Office Front Facade Redesign - ideas needed

Kindly read this brief thoroughly as there are 2 deliverables:
1. Office building façade redesign (see attached logo and also photo of our office building façade)
2. I also require a design for a freestanding signboard that will be coordinated with the design of the office front please see the images attached labelled signboard.

Deliverable number 1:
I am looking for a minimalist contemporary design with strong colours to draw the attention of the passing Traffic.

The office facade is to be repainted so you may choose to recolour the office in any way to coordinate with logo however the attached logo must remain as is. I prefer the colours red black and white or shades of these colours.

Velko property managers is a new company looking to target property investors in the local area. Most of our clients are from a middle to upper income demographic. We help these investors to rent out their properties and ensure they are maintained in good condition and provide a regular income.

The area we operate in is centrally located and close to the central business district of Perth.

Our office is situated in a residential area on a busy road facing diagonally at 45° down the road. People see our office from their cars whilst driving to work, there is no pedestrian traffic in the area. Therefore the office façade needs to stand out and any signage must be read by quickly passing traffic or convey our brand in seconds. Whilst the view of the office from the road is obscured somewhat by trees from a distance, once within 50 to 100 m of the office the full face of the office front is visible facing directly at the driver.

No measurements are provided for the façade of the office (please see the photo provided), this is a blank canvas as the whole building will be repainted to fit in with YOUR design. A logo is also attached. The colours red black and white are preferred.

Please provide an image of the office with signage/colours superimposed.

Deliverable number 2:
Also attached is an image of a freestanding sign for which I require a design. This sign is used for advertising properties for lease or sale which will be erected outside the front of residential houses. Again this sign needs to be bold and bright with a contemporary design. It needs to stand out from the crowd of many other signs in the area, whilst the sign advertises the property it must also promote our company brand by having a prominent logo. The size of these signboards will either be 1250 mm x 900 mm or 1800 mm x 625 mm. Please note that this sign must be rectangular in shape and cannot have any text or logo protruding outside of the lines of the rectangular sign due to cost restrictions.

Target Market(s)

Industry/Entity Type

Real Estate

Font styles to use
Sans Serif

Colors
ec1f27
ffffff
000000

Requirements
Must have
• Contemporary uncluttered design using the colours red black and white of shades of.
Nice to have
• A prominent logo with the words "Property Managers" easily read by passing traffic.
• Files provided with editable text and the name of the font used.
Should not have
• designs protruding outside of the overall building facia or sign rectangle.

```html
<!DOCTYPE html>
<html lang="en">
<head>
<meta charset="utf-8">
<title>Velko Property Managers – For Lease Signboard</title>
<link href="https://fonts.googleapis.com/css2?family=Raleway:wght@300;400;800&family=Roboto:wght@300;700&display=swap" rel="stylesheet">
<style>
  :root {
    --slate: #364046;
    --red: #ec1f27;
    --white: #ffffff;
    --ink: #364046;
  }
  * { margin: 0; padding: 0; box-sizing: border-box; }
  html, body {
    width: 897px;
    height: 1200px;
    overflow: hidden;
    background: var(--slate);
  }
  .signboard {
    position: relative;
    width: 897px;
    height: 1200px;
    background: var(--slate);
    font-family: "Raleway", sans-serif;
    color: var(--ink);
  }
  .signboard__frame {
    position: absolute;
    inset: 0;
  }
  .line {
    position: absolute;
    left: 0;
    width: 100%;
    text-align: center;
    white-space: nowrap;
  }
  .brand-mark {
    position: absolute;
    left: 358px;
    top: 112px;
    width: 180px;
    height: 180px;
    background: var(--red);
  }
  .brand-name {
    top: 370px;
    font-family: "Raleway", sans-serif;
    font-weight: 300;
    font-size: 128px;
    line-height: 130px;
    letter-spacing: 34px;
    padding-left: 34px;
    color: var(--ink);
  }
  .brand-tagline {
    top: 578px;
    font-family: "Raleway", sans-serif;
    font-weight: 400;
    font-size: 38px;
    line-height: 40px;
    letter-spacing: 7px;
    padding-left: 7px;
    color: var(--ink);
    transform: translateY(-52px);
  }
  .listing-type {
    top: 640px;
    font-size: 146px;
    line-height: 150px;
    color: var(--white);
    font-weight: 400;
  }
  .listing-type strong { font-weight: 800; }
  .contact-label {
    font-family: "Roboto", sans-serif;
    font-weight: 300;
    font-size: 37px;
    line-height: 40px;
    color: var(--red);
  }
  .contact-label--office { top: 836px; }
  .contact-label--mobile { top: 980px; }
  .contact-number {
    font-family: "Roboto", sans-serif;
    font-weight: 700;
    font-size: 94px;
    line-height: 100px;
    color: var(--ink);
  }
  .contact-number--office { top: 866px; }
  .contact-number--mobile { top: 1016px; }
  .web-address {
    top: 1124px;
    font-family: "Roboto", sans-serif;
    font-size: 60px;
    line-height: 64px;
    letter-spacing: 2px;
    color: var(--white);
  }
  .web-address b { font-weight: 700; }
  .web-address span { font-weight: 300; }
</style>
</head>
<body>
<main class="signboard">
  <svg class="signboard__frame" width="897" height="1200" viewBox="0 0 897 1200" aria-hidden="true">
    <rect class="header-panel" x="50" y="42" width="797" height="570" fill="#ffffff"/>
    <rect class="listing-band" x="0" y="608" width="897" height="218" fill="#ec1f27"/>
    <polygon class="contact-panel" points="177,825 717,825 837,1102 60,1102" fill="#ffffff"/>
  </svg>

  <div class="brand-mark" aria-hidden="true"></div>
  <div class="line brand-name">VELKO</div>
  <div class="line brand-tagline">PROPERTY MANAGERS</div>

  <div class="line listing-type">FOR <strong>LEASE</strong></div>

  <div class="line contact-label contact-label--office">OFFICE</div>
  <div class="line contact-number contact-number--office">9455 0281</div>
  <div class="line contact-label contact-label--mobile">MOBILE</div>
  <div class="line contact-number contact-number--mobile">0400 318 742</div>

  <div class="line web-address"><b>VELKO</b><span>PROPERTY</span><b>.COM.AU</b></div>
</main>
</body>
</html>
```